Website update for Harborline Ledger Partners & Bookkeeping

Our website needs updating
www.harborlineledgerpartners.com
Here are some of our latest print pieces to use as a guide?
I have also attached our graphic identity guide which includes the Pantone colors

Target Market(s)

Insurance Agencies

Industry/Entity Type

Accounting

Number of Pages Required

5+ page

```html
<!DOCTYPE html>
<html lang="en">
<head>
<meta charset="utf-8">
<title>Harborline Ledger Partners &amp; Bookkeeping</title>
<link href="https://fonts.googleapis.com/css2?family=Oswald:wght@400;500;600&family=Open+Sans:wght@400;600;700&display=swap" rel="stylesheet">
<style>
:root{
  --teal:#22b3a2;
  --teal-dark:#168c7f;
  --teal-deep:#0e5a55;
  --footer:#0c4b47;
  --ink:#2d3436;
  --muted:#6b7274;
  --light:#f3f6f6;
  --white:#ffffff;
}
*{box-sizing:border-box;margin:0;padding:0}
html,body{width:1200px;height:3132px;overflow:hidden}
body{font-family:"Open Sans",Arial,sans-serif;color:var(--ink);background:var(--white);position:relative}
.heading{font-family:"Oswald","Arial Narrow",sans-serif;font-weight:500;text-transform:uppercase;color:var(--ink);letter-spacing:1px}

/* header */
.site-header{position:absolute;top:0;left:0;width:1200px;height:72px;background:rgba(255,255,255,.92);z-index:3;display:flex;align-items:center;justify-content:space-between;padding:0 40px 0 36px}
.brand{display:flex;align-items:center;gap:12px;margin-top:40px;background:var(--white);padding:14px 18px;box-shadow:0 2px 8px rgba(0,0,0,.12)}
.brand-square{width:34px;height:34px;background:var(--teal)}
.brand-name{font-family:"Oswald",sans-serif;font-weight:500;font-size:19px;line-height:1.15;color:var(--teal-deep);width:220px;text-transform:uppercase}
.main-nav{display:flex;gap:6px;align-self:flex-start}
.main-nav a{font-family:"Oswald",sans-serif;font-size:15px;color:var(--ink);text-decoration:none;padding:24px 18px 14px;text-transform:none}
.main-nav a.active{background:var(--teal);color:var(--white)}

/* hero */
.hero{position:absolute;top:0;left:0;width:1200px;height:620px}
.hero-photo{position:absolute;inset:0;background:linear-gradient(160deg,#e9e4dc 0%,#c9b8a5 40%,#8f7a68 70%,#d8d2c8 100%)}
.hero-wave{position:absolute;left:0;bottom:0;width:1200px;height:140px}

/* about */
.about{position:absolute;top:620px;left:0;width:1200px;height:400px;text-align:center}
.about-map{position:absolute;left:300px;top:20px;width:600px;height:300px;background:radial-gradient(ellipse at center,rgba(34,179,162,.10),rgba(34,179,162,0) 70%)}
.about-kicker{position:relative;padding-top:38px;font-size:16px;color:var(--muted);font-weight:600}
.about-title{position:relative;font-size:60px;line-height:1.1}
.about-text{position:relative;width:640px;margin:14px auto 0;font-size:13.5px;line-height:1.55;color:var(--muted)}
.btn{display:inline-block;font-family:"Oswald",sans-serif;font-size:14px;letter-spacing:1px;text-transform:uppercase;color:var(--white);background:var(--teal);padding:10px 22px}
.about .btn{position:relative;margin-top:24px;background:var(--teal-deep)}

/* services */
.services{position:absolute;top:1030px;left:0;width:1200px;height:480px;background:linear-gradient(180deg,var(--teal) 0%,#1fa696 100%);text-align:center}
.services-title{color:var(--white);font-size:58px;padding-top:48px}
.services-row{display:flex;justify-content:center;gap:40px;margin-top:36px}
.service{width:200px;color:var(--white)}
.service-icon{width:64px;height:64px;margin:0 auto 14px;border-radius:50%;background:rgba(255,255,255,.18);display:flex;align-items:center;justify-content:center}
.service-name{font-family:"Oswald",sans-serif;font-size:17px;line-height:1.2;text-transform:uppercase;height:42px}
.service-text{font-size:12px;line-height:1.5;opacity:.9;margin-top:12px}
.service-more{font-family:"Oswald",sans-serif;font-size:13px;margin-top:12px;letter-spacing:1px}
.slider-arrow{position:absolute;top:300px;width:24px;height:40px}
.slider-arrow.prev{left:30px}.slider-arrow.next{right:30px}
.down-circle{position:absolute;left:576px;width:48px;height:48px;border-radius:50%;background:var(--white);box-shadow:0 2px 6px rgba(0,0,0,.2);display:flex;align-items:center;justify-content:center}
.services .down-circle{top:456px}

/* how it works */
.how{position:absolute;top:1510px;left:0;width:1200px;height:740px}
.how-title{text-align:center;font-size:58px;padding-top:58px}
.steps{position:absolute;left:90px;top:170px;width:560px;list-style:none}
.step{display:flex;align-items:flex-start;gap:20px;margin-bottom:34px}
.step-mark{flex:none;width:30px;height:30px;border-radius:50%;background:#4d5557;display:flex;align-items:center;justify-content:center}
.step.first .step-mark{width:44px;height:44px;background:var(--teal);margin-left:-7px}
.step-text{font-size:13.5px;line-height:1.5;color:var(--ink);padding-top:5px}
.how-photo{position:absolute;left:770px;top:190px;width:300px;height:500px;background:linear-gradient(180deg,#ffffff 0%,#ede7e2 30%,#3a3434 65%,#222 100%);border-radius:150px 150px 0 0}
.how .down-circle{top:700px;border:1px solid #d6dada}

/* team */
.team{position:absolute;top:2250px;left:0;width:1200px;height:480px;text-align:center;background:var(--light)}
.team-title{font-size:58px;color:var(--teal);padding-top:34px}
.team-grid{display:flex;justify-content:center;gap:20px;margin-top:28px}
.member{width:250px}
.member-photo{height:240px}
.member:nth-child(1) .member-photo{background:linear-gradient(180deg,#3fc1b1,#1b9e90)}
.member:nth-child(2) .member-photo{background:linear-gradient(180deg,#8a7a6d,#3f3833)}
.member:nth-child(3) .member-photo{background:linear-gradient(180deg,#c9c2b2,#6f6a66)}
.member:nth-child(4) .member-photo{background:linear-gradient(180deg,#b4a99c,#4c4340)}
.member-name{font-family:"Oswald",sans-serif;font-size:16px;margin-top:12px}
.member-role{font-size:11.5px;line-height:1.4;color:var(--muted);margin-top:4px}
.team .btn{margin-top:22px;background:var(--teal-deep)}

/* newsletter */
.newsletter{position:absolute;top:2740px;left:0;width:1200px;height:228px;background:var(--teal);text-align:center;color:var(--white)}
.newsletter-title{font-family:"Oswald",sans-serif;font-size:40px;padding-top:32px;font-weight:500}
.newsletter-sub{font-size:13px;opacity:.9;margin-top:4px}
.newsletter-form{display:flex;justify-content:center;gap:16px;margin-top:26px}
.field{width:300px;height:40px;background:var(--white);color:#9aa0a2;font-size:12.5px;text-align:left;padding:11px 14px}
.newsletter .btn{background:var(--teal-deep);height:40px;padding:10px 26px}

/* footer */
.site-footer{position:absolute;top:2968px;left:0;width:1200px;height:164px;background:var(--footer);color:#d7ecea;font-size:13px}
.footer-row{display:flex;align-items:center;gap:60px;padding:44px 80px 0}
.footer-item{display:flex;align-items:center;gap:10px;line-height:1.4}
.social{margin-left:auto;display:flex;gap:12px}
.social span{width:30px;height:30px;border-radius:50%;background:rgba(255,255,255,.16);display:block}
.copyright{text-align:center;font-size:12px;margin-top:44px;opacity:.8}
</style>
</head>
<body>

<section class="hero">
  <div class="hero-photo" role="img" aria-label="Photo of a smiling family of four lying together on the floor"></div>
  <svg class="hero-wave" viewBox="0 0 1200 140" preserveAspectRatio="none" aria-hidden="true">
    <polygon points="0,60 260,110 520,50 800,100 1000,40 1200,80 1200,140 0,140" fill="#ffffff"/>
    <polyline points="0,60 260,110 520,50 800,100 1000,40 1200,80" fill="none" stroke="#22b3a2" stroke-width="4"/>
  </svg>
</section>

<header class="site-header">
  <div class="brand">
    <span class="brand-square"></span>
    <span class="brand-name">Harborline Ledger Partners &amp; Bookkeeping</span>
  </div>
  <nav class="main-nav">
    <a class="active">Home</a><a>About Us</a><a>Company</a><a>Our Services</a><a>How It Works</a><a>Resources</a><a>Contact Us</a><a>Blog</a>
  </nav>
</header>

<section class="about">
  <div class="about-map" role="img" aria-label="Faint world map in the background"></div>
  <p class="about-kicker">Know About</p>
  <h2 class="heading about-title">The HLPB</h2>
  <p class="about-text">HLPB is a professional Accounting/Bookkeeping firm located in Connecticut dedicated exclusively to Independent Insurance Agencies. After working in-house at agencies for many years, Maren Okafor founded HLPB in 2011 to help Independent Insurance Agencies manage their accounting and bookkeeping. HLPB currently has 13 staff members working in our Connecticut office cross-trained in all aspects of AgencyDesk accounting. We have just added the capacity for 8 additional staff members. Call us, we'll be ready to meet your unique needs.</p>
  <span class="btn">Learn More</span>
</section>

<section class="services">
  <h2 class="heading services-title">Services Available</h2>
  <svg class="slider-arrow prev" viewBox="0 0 24 40" aria-hidden="true"><polyline points="20,4 4,20 20,36" fill="none" stroke="#fff" stroke-width="3"/></svg>
  <svg class="slider-arrow next" viewBox="0 0 24 40" aria-hidden="true"><polyline points="4,4 20,20 4,36" fill="none" stroke="#fff" stroke-width="3"/></svg>
  <div class="services-row">
    <div class="service">
      <div class="service-icon"><svg width="32" height="32" viewBox="0 0 32 32"><rect x="6" y="3" width="20" height="26" fill="none" stroke="#fff" stroke-width="2"/><line x1="10" y1="10" x2="22" y2="10" stroke="#fff" stroke-width="2"/><line x1="10" y1="16" x2="22" y2="16" stroke="#fff" stroke-width="2"/><line x1="10" y1="22" x2="18" y2="22" stroke="#fff" stroke-width="2"/></svg></div>
      <div class="service-name">Record Direct Bill Commission</div>
      <p class="service-text">Lorem ipsum is simply dummy text of the printing and typesetting</p>
      <div class="service-more">KNOW MORE</div>
    </div>
    <div class="service">
      <div class="service-icon"><svg width="32" height="32" viewBox="0 0 32 32"><rect x="3" y="8" width="26" height="16" fill="none" stroke="#fff" stroke-width="2"/><circle cx="16" cy="16" r="4" fill="none" stroke="#fff" stroke-width="2"/></svg></div>
      <div class="service-name">Reconcile &amp; Pay Agency Bill Premiums</div>
      <p class="service-text">Lorem ipsum is simply dummy text of the printing and typesetting</p>
      <div class="service-more">KNOW MORE</div>
    </div>
    <div class="service">
      <div class="service-icon"><svg width="32" height="32" viewBox="0 0 32 32"><rect x="5" y="5" width="22" height="22" fill="none" stroke="#fff" stroke-width="2"/><line x1="5" y1="12" x2="27" y2="12" stroke="#fff" stroke-width="2"/><line x1="14" y1="12" x2="14" y2="27" stroke="#fff" stroke-width="2"/></svg></div>
      <div class="service-name">Reconcile General Ledger Accounts</div>
      <p class="service-text">Lorem ipsum is simply dummy text of the printing and typesetting</p>
      <div class="service-more">KNOW MORE</div>
    </div>
    <div class="service">
      <div class="service-icon"><svg width="32" height="32" viewBox="0 0 32 32"><rect x="4" y="5" width="24" height="17" fill="none" stroke="#fff" stroke-width="2"/><line x1="16" y1="22" x2="16" y2="27" stroke="#fff" stroke-width="2"/><line x1="10" y1="27" x2="22" y2="27" stroke="#fff" stroke-width="2"/></svg></div>
      <div class="service-name">Prepare &amp; Internet Financial Statements</div>
      <p class="service-text">Lorem ipsum is simply dummy text of the printing and typesetting</p>
      <div class="service-more">KNOW MORE</div>
    </div>
  </div>
  <div class="down-circle"><svg width="18" height="12" viewBox="0 0 18 12"><polyline points="2,2 9,9 16,2" fill="none" stroke="#22b3a2" stroke-width="2.5"/></svg></div>
</section>

<section class="how">
  <h2 class="heading how-title">How It Works</h2>
  <ul class="steps">
    <li class="step first"><span class="step-mark"><svg width="18" height="18" viewBox="0 0 18 18"><path d="M9 2v14M2 9h14" stroke="#fff" stroke-width="3"/></svg></span><span class="step-text">Agencies route documents to HLPB through AgencyDesk, typically incorporating the process into an existing workflow.</span></li>
    <li class="step"><span class="step-mark"><svg width="12" height="12" viewBox="0 0 12 12"><polyline points="4,2 8,6 4,10" fill="none" stroke="#fff" stroke-width="2"/></svg></span><span class="step-text">On an agreed upon schedule HLPB creates checks in AgencyDesk...</span></li>
    <li class="step"><span class="step-mark"><svg width="12" height="12" viewBox="0 0 12 12"><polyline points="4,2 8,6 4,10" fill="none" stroke="#fff" stroke-width="2"/></svg></span><span class="step-text">HLPB communicates with your staff &amp; insurance company/broker...</span></li>
    <li class="step"><span class="step-mark"><svg width="12" height="12" viewBox="0 0 12 12"><polyline points="4,2 8,6 4,10" fill="none" stroke="#fff" stroke-width="2"/></svg></span><span class="step-text">Agencies make bank deposits &amp; upload to HLPB for recording.</span></li>
    <li class="step"><span class="step-mark"><svg width="12" height="12" viewBox="0 0 12 12"><polyline points="4,2 8,6 4,10" fill="none" stroke="#fff" stroke-width="2"/></svg></span><span class="step-text">HLPB downloads commission statements from company websites...</span></li>
    <li class="step"><span class="step-mark"><svg width="12" height="12" viewBox="0 0 12 12"><polyline points="4,2 8,6 4,10" fill="none" stroke="#fff" stroke-width="2"/></svg></span><span class="step-text">Financial statements are emailed to Agency Principals early each month...</span></li>
  </ul>
  <div class="how-photo" role="img" aria-label="Photo of a smiling businesswoman holding an open folder"></div>
  <div class="down-circle"><svg width="18" height="12" viewBox="0 0 18 12"><polyline points="2,2 9,9 16,2" fill="none" stroke="#8a9193" stroke-width="2.5"/></svg></div>
</section>

<section class="team">
  <h2 class="heading team-title">Meet The Team</h2>
  <div class="team-grid">
    <div class="member"><div class="member-photo" role="img" aria-label="Portrait photo of team member Maren Okafor"></div><div class="member-name">Maren Okafor</div><div class="member-role">Principal</div></div>
    <div class="member"><div class="member-photo" role="img" aria-label="Portrait photo of team member Tobias Lindqvist"></div><div class="member-name">Tobias Lindqvist</div><div class="member-role">Accountant and Financial Analyst for Northgate Systems Agencies</div></div>
    <div class="member"><div class="member-photo" role="img" aria-label="Portrait photo of team member Camila Strand"></div><div class="member-name">Camila Strand</div><div class="member-role">Accounting Associate and Office Manager</div></div>
    <div class="member"><div class="member-photo" role="img" aria-label="Portrait photo of team member Priya Halvorsen"></div><div class="member-name">Priya Halvorsen</div><div class="member-role">Client Relations Manager</div></div>
  </div>
  <span class="btn">View All</span>
</section>

<section class="newsletter">
  <h2 class="newsletter-title">Newsletter</h2>
  <p class="newsletter-sub">Lorem Ipsum is simply dummy text - Subscribe to our monthly agency updates</p>
  <div class="newsletter-form">
    <div class="field">Enter name</div>
    <div class="field">Enter E-mail</div>
    <span class="btn">Subscribe</span>
  </div>
</section>

<footer class="site-footer">
  <div class="footer-row">
    <div class="footer-item"><svg width="18" height="22" viewBox="0 0 18 22"><path d="M9 1a7 7 0 0 1 7 7c0 5-7 13-7 13S2 13 2 8a7 7 0 0 1 7-7z" fill="#22b3a2"/><circle cx="9" cy="8" r="2.5" fill="#0c4b47"/></svg><span>HLPB · 48 Tidewater Lane<br>Harbor Falls, CT 06999</span></div>
    <div class="footer-item"><svg width="18" height="18" viewBox="0 0 18 18"><path d="M4 1l3 4-2 2c1 2 3 4 5 5l2-2 4 3-2 3C8 16 2 10 1 4z" fill="#22b3a2"/></svg><span>860-555-0142</span></div>
    <div class="footer-item"><svg width="20" height="14" viewBox="0 0 20 14"><rect x="1" y="1" width="18" height="12" fill="none" stroke="#22b3a2" stroke-width="2"/><polyline points="1,1 10,8 19,1" fill="none" stroke="#22b3a2" stroke-width="2"/></svg><span>info@harborlineledgerpartners.com</span></div>
    <div class="social"><span></span><span></span><span></span></div>
  </div>
  <p class="copyright">© Harborline Ledger Partners &amp; Bookkeeping · 2015. All rights reserved.</p>
</footer>

</body>
</html>
```